Popup Nightclub Grand Opening Flyer

We need to design a flyer for the grand opening of an upscale, exclusive nightclub called "Lantern". The design needs to be chic and exclusive. The background should be black and the text should primarily be white. We like minimalist designs.

Here is the text for the flyer
-
Velvetroll Atlanta Presents

Lantern (LOGO)

A Popup Nightclub Experience
For one night Only

Friday, October 18, 2013
Party begins at 9PM

INVITE ONLY

See invitation for location details
(Velvetroll Atlanta logo)

-
Examples we like

http://cdn4-x.pressfolio-example.com/sites/default/files/styles/image_content_width/hash/3b/fd/2468013579_4421_flyer.jpg?itok=K9rtQw2z

http://files.hubspace-example.net/files/8Hqq-Tr72WWE3kaRbTmcxP5QZK2F396J8nbRw4CKMHfdX2Y7qSEF-MqjxDoNrLY3QCyQJD7npjGaRq3k-Mhx6hqf3MDSWf8r3/2zenSaturdays.jpg

http://morvex-example.com/wp-content/uploads/siteskin/widgetkit/gallery/2zen/2zen-gen_qstay4-01.jpg

Hi All, one thing that we are seeing that we don't like is on over emphasis on the phrase "a popup nightclub experience" please don't make this the largest thing on the flyer

Target Market(s)

Target market is 25-35 year olds who are affluent (rich) and like luxury brands

Requirements
Must have
• Dark Background
Nice to have
• Velvetroll Logo on the bottom
Modern text that isn't curvy
Should not have
• Curved text

```html
<!DOCTYPE html>
<html lang="en">
<head>
<meta charset="utf-8">
<title>Lantern Nightclub – A Popup Nightclub Experience</title>
<link rel="stylesheet" href="https://fonts.googleapis.com/css2?family=Raleway:wght@200;300;400;500&family=Josefin+Sans:wght@400;600&family=Bodoni+Moda:wght@600&family=Arimo:wght@400;500;700&display=swap">
<style>
  :root {
    --bg: #0b0b0b;
    --bg-soft: #1d1d1d;
    --ink: #ffffff;
    --silver-light: #f4f4f4;
    --silver: #cfcfcf;
    --silver-mid: #a9a9a9;
    --silver-dark: #7a7a7a;
    --banner-ink: #111111;
  }
  * { margin: 0; padding: 0; box-sizing: border-box; }
  html, body { width: 776px; height: 1200px; overflow: hidden; background: var(--bg); }
  .flyer {
    position: relative;
    width: 776px;
    height: 1200px;
    overflow: hidden;
    color: var(--ink);
    font-family: "Raleway", sans-serif;
    font-variant-numeric: lining-nums;
    text-align: center;
  }
  .flyer__texture {
    position: absolute; inset: 0;
    background: radial-gradient(ellipse at 50% 45%, var(--bg-soft) 0%, var(--bg) 78%);
  }
  .abs { position: absolute; left: 0; width: 100%; }
  .presenter { top: 56px; font-size: 22px; font-weight: 400; letter-spacing: 1.5px; }
  .brand-mark { position: absolute; left: 318px; top: 98px; width: 140px; height: 140px; }
  .brand-name { top: 288px; font-size: 62px; font-weight: 300; letter-spacing: 10px; line-height: 1; padding-left: 10px; }
  .brand-sub { top: 362px; font-size: 28px; font-weight: 400; letter-spacing: 3px; line-height: 1; }
  .headline { top: 424px; font-family: "Josefin Sans", sans-serif; font-weight: 400; line-height: 1; }
  .headline__line { display: block; }
  .headline__line--sm { font-size: 48px; }
  .headline__line--lg { font-size: 56px; margin-top: 6px; }
  .headline__line--md { font-size: 46px; margin-top: 8px; }
  .ribbon { position: absolute; left: 0; top: 588px; width: 776px; height: 140px; }
  .ribbon__label {
    top: 681px; font-size: 21px; letter-spacing: 2.5px; color: var(--banner-ink); font-weight: 400; line-height: 1;
  }
  .rule { position: absolute; left: 155px; width: 470px; height: 3px; background: var(--ink); }
  .rule--top { top: 774px; }
  .rule--bottom { top: 897px; }
  .date { top: 805px; font-size: 38px; line-height: 1; white-space: nowrap; }
  .date__day { font-family: "Raleway", sans-serif; font-weight: 200; }
  .date__month { font-family: "Bodoni Moda", serif; font-weight: 600; }
  .date__num { font-family: "Arimo", sans-serif; font-weight: 700; }
  .time { top: 856px; font-family: "Arimo", sans-serif; font-size: 23px; letter-spacing: 0.5px; font-weight: 400; line-height: 1; }
  .invite { position: absolute; left: 170px; top: 938px; width: 436px; height: 68px; }
  .invite__label {
    top: 946px; font-family: "Arimo", sans-serif; font-size: 36px; font-weight: 500;
    color: var(--banner-ink); letter-spacing: 0.5px; line-height: 1;
  }
  .note { top: 1043px; font-size: 18px; letter-spacing: 3.2px; font-weight: 400; line-height: 1; }
  .host {
    position: absolute; left: 178px; top: 1068px; height: 74px;
    display: flex; align-items: center; gap: 26px;
  }
  .host__dot { width: 58px; height: 58px; border-radius: 50%; border: 2px solid var(--ink); }
  .host__divider { width: 2px; height: 70px; background: var(--ink); }
  .host__text { text-align: left; line-height: 1; }
  .host__name { display: block; font-size: 42px; font-weight: 300; letter-spacing: 2px; }
  .host__city { display: block; font-size: 15px; font-weight: 400; letter-spacing: 3px; margin-top: 6px; }
</style>
</head>
<body>
<main class="flyer">
  <div class="flyer__texture" role="img" aria-label="Dark black damask swirl pattern background"></div>

  <p class="abs presenter">VELVETROLL ATLANTA PRESENTS</p>

  <svg class="brand-mark" viewBox="0 0 140 140" aria-hidden="true">
    <circle cx="70" cy="70" r="66" fill="none" stroke="var(--silver)" stroke-width="4"/>
  </svg>
  <h1 class="abs brand-name">LANTERN</h1>
  <p class="abs brand-sub">NIGHTCLUB</p>

  <h2 class="abs headline">
    <span class="headline__line headline__line--sm">A POPUP</span>
    <span class="headline__line headline__line--lg">NIGHTCLUB</span>
    <span class="headline__line headline__line--md">EXPERIENCE</span>
  </h2>

  <svg class="ribbon" viewBox="0 0 776 140" aria-hidden="true">
    <defs>
      <linearGradient id="ribbonTail" x1="0" y1="0" x2="0" y2="1">
        <stop offset="0" stop-color="#f4f4f4"/>
        <stop offset="1" stop-color="#9a9a9a"/>
      </linearGradient>
      <linearGradient id="ribbonBand" x1="0" y1="0" x2="0" y2="1">
        <stop offset="0" stop-color="#ffffff"/>
        <stop offset="1" stop-color="#dcdcdc"/>
      </linearGradient>
    </defs>
    <path d="M2 14 Q110 6 230 60 L230 118 Q120 62 14 70 L34 42 Z" fill="url(#ribbonTail)"/>
    <path d="M774 14 Q666 6 546 60 L546 118 Q656 62 762 70 L742 42 Z" fill="url(#ribbonTail)"/>
    <path d="M204 72 Q388 94 572 72 L572 124 Q388 140 204 124 Z" fill="url(#ribbonBand)"/>
  </svg>
  <p class="abs ribbon__label">FOR ONE NIGHT ONLY</p>

  <div class="rule rule--top"></div>
  <p class="abs date"><span class="date__day">FRIDAY</span>, <span class="date__month">OCTOBER</span> <span class="date__num">18, 2013</span></p>
  <p class="abs time">PARTY BEGINS AT 9PM</p>
  <div class="rule rule--bottom"></div>

  <svg class="invite" viewBox="0 0 436 68" aria-hidden="true">
    <polygon points="0,14 48,14 48,66 0,66 18,40" fill="var(--silver-dark)"/>
    <polygon points="436,14 388,14 388,66 436,66 418,40" fill="var(--silver-dark)"/>
    <rect x="42" y="2" width="352" height="54" fill="var(--ink)" stroke="var(--silver)" stroke-width="2"/>
  </svg>
  <p class="abs invite__label">INVITE ONLY</p>

  <p class="abs note">SEE INVITATION FOR LOCATION DETAILS</p>

  <div class="host">
    <span class="host__dot" aria-hidden="true"></span>
    <span class="host__divider" aria-hidden="true"></span>
    <span class="host__text">
      <span class="host__name">VELVETROLL</span>
      <span class="host__city">ATLANTA</span>
    </span>
  </div>
</main>
</body>
</html>
```